Business card design for holistic health care clinic

We need a double-sided business card design for our holistic health care clinic that integrates our logo design and also its color scheme. My business is called Valmira. It is an integrative medicine clinic. You have already done the logo for me. Please ensure an elegant and upscale design that is not cluttered, but still has all the necessary information (please see below for details).

Target Market(s)

Wellness, fitness, rehabilitation for educated, well-traveled open-minded clients who are focused on natural, organic, balanced and preventive healthcare and lifestyle.

Industry/Entity Type

Medical

Contact Information for Business Card

Modern, clean.

Number of Pages Required

1 page

Font styles to use
Serif
Sans Serif

Colors

Designer to choose colors to be used in the design.

Requirements
Must have
• Logo on one side, all other information on the other side.
• Other information should include:
• Tobias Wrenfeld - DOE, CPT, LMT
• 4100 East Marrow Drive
• Austin, TX 78119
• 512 555 0148
• 818 555 0192
• info@ValmiraHealth.example
• t.wrenfeld@ValmiraHealth.example
Nice to have
• Darker background on front - but not totally black - shaded/dark gray.

```html
<!DOCTYPE html>
<html lang="en">
<head>
<meta charset="utf-8">
<title>Valmira – Business Card</title>
<link href="https://fonts.googleapis.com/css2?family=Source+Sans+3:wght@400;600;700&display=swap" rel="stylesheet">
<style>
  :root {
    --backdrop: #636363;
    --card: #262626;
    --brand-blue: #0794d0;
    --text-light: #f2f2f2;
  }
  * { margin: 0; padding: 0; box-sizing: border-box; }
  html, body { width: 1200px; height: 900px; overflow: hidden; }
  body {
    background: var(--backdrop);
    font-family: "Source Sans 3", "Helvetica Neue", Arial, sans-serif;
    position: relative;
  }
  .card {
    position: absolute;
    top: 305px;
    height: 272px;
    background: var(--card);
    border-radius: 12px;
    overflow: hidden;
    color: var(--text-light);
    text-align: center;
  }
  .card--contact { left: 149px; width: 439px; }
  .card--brand { left: 608px; width: 441px; }

  .top-band { position: absolute; left: 0; top: 0; width: 100%; height: 60px; }
  .contact-brand {
    position: absolute;
    left: 0; right: 0; top: 62px;
    font-size: 46px;
    font-weight: 700;
    letter-spacing: 1px;
    color: var(--text-light);
    text-transform: uppercase;
  }
  .person { position: absolute; left: 0; right: 0; top: 150px; font-size: 11.5px; }
  .person-name {
    color: var(--brand-blue);
    font-weight: 700;
    font-size: 14px;
    letter-spacing: .3px;
    margin-right: 5px;
  }
  .address { position: absolute; left: 0; right: 0; top: 181px; font-size: 12px; }
  .contact-lines {
    position: absolute; left: 0; right: 0; top: 213px;
    font-size: 12px; line-height: 16px;
  }
  .label { color: var(--brand-blue); font-weight: 600; }
  .sep { margin: 0 3px; }

  .wordmark {
    position: absolute; left: 0; right: 0; top: 108px;
    font-size: 54px; font-weight: 700; line-height: 1;
    color: var(--brand-blue);
    text-transform: uppercase;
  }
  .tagline {
    position: absolute; left: 0; right: 0; top: 168px;
    font-size: 15.5px; font-weight: 600;
    color: var(--brand-blue);
  }
  .website { position: absolute; left: 0; right: 0; top: 226px; font-size: 12.5px; }
</style>
</head>
<body>
  <section class="card card--contact">
    <svg class="top-band" viewBox="0 0 439 60" preserveAspectRatio="none" aria-hidden="true">
      <path d="M0 0 H439 V36 Q330 18 219.5 44 Q110 18 0 36 Z" fill="var(--brand-blue)"/>
    </svg>
    <div class="contact-brand">Valmira</div>
    <p class="person"><span class="person-name">TOBIAS WRENFELD</span>DOE, CPT, LMT</p>
    <p class="address">4100 East Marrow Drive Austin, TX 78119</p>
    <div class="contact-lines">
      <p><span class="label">P:</span> 512 555 0148<span class="sep">|</span><span class="label">M:</span> 818 555 0192</p>
      <p><span class="label">E:</span> info@ValmiraHealth.example<span class="sep">|</span><span class="label">E:</span> t.wrenfeld@ValmiraHealth.example</p>
    </div>
  </section>

  <section class="card card--brand">
    <div class="wordmark">Valmira</div>
    <p class="tagline">Integrative Holistic Medicine</p>
    <p class="website">www.ValmiraHealth.example</p>
  </section>
</body>
</html>
```